VENTURE CAPITAL GROUP BUSINESS CARD DESIGN

Venture Capital Group based in SF looking for a bold business card design. No trendy colour explosion, 3D effects etc. Just "simple" optical effects. Works on your brain, keeps your eye focused and sticks to your mind.
Target Market(s)
Technology startups
Industry/Entity Type
Venture Capital
Contact Information for Business Card
DESMOND WHITLAKE
MANAGING PARTNER
187 FENWORTH ST SAN FRANCISCO, CA 94187
415.555.0142 O
415.555.0147 F
415.555.0193 C
desmond@veldtmoorcapital.ventures

```html
<!DOCTYPE html>
<html lang="en">
<head>
<meta charset="utf-8">
<title>Veldtmoor Capital Group — Business Card</title>
<link rel="stylesheet" href="https://fonts.googleapis.com/css2?family=Crimson+Text:wght@400;600;700&display=swap">
<style>
  :root{
    --bg:#2b2b2b;
    --card:#f4f4f4;
    --card-edge:#e2e2e2;
    --green:#1e8a3a;
    --green-dark:#14652a;
    --green-band:#25913f;
    --ink:#2a2a2a;
    --facet-light:#fafafa;
    --facet-mid:#dcdcdc;
    --divider:#9a9a9a;
  }
  *{margin:0;padding:0;box-sizing:border-box}
  html,body{width:1200px;height:873px;overflow:hidden}
  body{background:var(--bg);font-family:"Crimson Text",Georgia,serif;position:relative}

  .card{position:absolute;width:540px;height:309px;background:var(--card);
        box-shadow:0 10px 30px rgba(0,0,0,.45);overflow:hidden}

  /* back of card */
  .card-back{left:50px;top:110px}
  .card-back .facets{position:absolute;inset:0;
        background:linear-gradient(135deg,var(--facet-light) 0%,var(--facet-mid) 45%,var(--facet-light) 70%,var(--facet-mid) 100%)}
  .card-back .brand{position:absolute;inset:0;display:flex;flex-direction:column;
        align-items:center;justify-content:center;gap:14px}
  .brand-dot{width:54px;height:54px;border-radius:50%;background:var(--green)}
  .brand-name{color:var(--green);font-weight:600;font-size:34px;letter-spacing:2px;text-transform:uppercase}

  /* front of card */
  .card-front{left:610px;top:450px}
  .front-logo{position:absolute;left:0;top:0;width:240px;height:232px;display:flex;
        flex-direction:column;align-items:center;justify-content:center;gap:12px}
  .front-logo .brand-dot{width:46px;height:46px}
  .front-logo .brand-name{font-size:25px;letter-spacing:1.5px}
  .divider{position:absolute;left:240px;top:22px;width:1.5px;height:150px;
        background:linear-gradient(to bottom,transparent,var(--divider) 50%,transparent)}
  .contact{position:absolute;left:268px;top:26px;color:var(--ink)}
  .person-name{color:var(--green-dark);font-weight:700;font-size:17px;line-height:1}
  .person-title{font-size:12px;margin-top:3px}
  .lines{list-style:none;margin-top:24px}
  .lines li{display:flex;align-items:center;gap:7px;font-size:13.5px;line-height:19px}
  .lines svg{width:12px;height:12px;fill:var(--green)}

  .band{position:absolute;left:0;right:0;bottom:0;height:84px;background:var(--green-band);
        display:flex;flex-direction:column;align-items:center;justify-content:center;gap:2px}
  .band-name{display:flex;align-items:center;gap:10px;color:#fff;font-weight:700;font-size:17px;letter-spacing:.5px}
  .band-name::before,.band-name::after{content:"";width:56px;height:1.5px;background:#fff}
  .band-address{color:var(--green-dark);font-size:15px}
</style>
</head>
<body>

<section class="card card-back">
  <div class="facets" role="img" aria-label="Soft grey faceted geometric background pattern"></div>
  <div class="brand">
    <span class="brand-dot"></span>
    <span class="brand-name">Veldtmoor Capital Group</span>
  </div>
</section>

<section class="card card-front">
  <div class="front-logo">
    <span class="brand-dot"></span>
    <span class="brand-name">Veldtmoor</span>
  </div>
  <div class="divider"></div>

  <div class="contact">
    <p class="person-name">Desmond Whitlake</p>
    <p class="person-title">Managing Partner</p>
    <ul class="lines">
      <li><svg viewBox="0 0 12 12" aria-hidden="true"><path d="M1 4c0-2 2-3 5-3s5 1 5 3v1H8V4H4v1H1zM2 6h8l1 5H1z"/></svg>415.555.0142</li>
      <li><svg viewBox="0 0 12 12" aria-hidden="true"><path d="M2 1l2 0 1 3-1.5 1c.7 1.6 1.9 2.8 3.5 3.5L8 7l3 1v2c0 .6-.4 1-1 1C5 11 1 7 1 2c0-.6.4-1 1-1z"/></svg>415.555.0147</li>
      <li><svg viewBox="0 0 12 12" aria-hidden="true"><path d="M3 1h6v3H3zM1 5h10v4H9V7H3v2H1zM3.5 8h5v3h-5z"/></svg>415.555.0193</li>
      <li><svg viewBox="0 0 12 12" aria-hidden="true"><path d="M1 2.5h10v7H1zM1.5 3l4.5 3.5L10.5 3" stroke="#f4f4f4" stroke-width=".8"/></svg>desmond@veldtmoorcapital.ventures</li>
    </ul>
  </div>

  <div class="band">
    <p class="band-name">VELDTMOOR CAPITAL GROUP</p>
    <p class="band-address">187 Fenworth St San Francisco, CA 94187</p>
  </div>
</section>

</body>
</html>
```